BrivoTerna. Lantern of the Steady Harvest. Business card

Professional business card for BrivoTerna (Lantern of the Steady Harvest)
My rationale: Strategy-> Execution-> Results-> Value that lead to the BrivoTerna name: We put the Lantern of the Steady Harvest.
We deliver value to our customers helping them at defining a good strategy (cyan arrow). 90% of well formulated strategies fail due to poor execution so we also consider strategical execution very important (green arrow). Due to the execution we obtain the results (blue arrow). Finally, the results provide feedback to redefine strategy, and the new strategy has to be executed and new results obtained providing new feedback and on and on. It's like a wheel that finally, must create corporate value: value for shareholders, staholders, employees, providers...-

Target Market(s)

CEOs and steering comitees , invewrnent funds

Industry/Entity Type

Business Consultant

Contact Information for Business Card

Teodoro Vinsquel
CEO & Founder
teodoro.vinsquel@brivoterna-example.com
Mobile: +34 655.803.912
www.brivoterna-example.com

Colors

Designer to choose colors to be used in the design.

Requirements
Nice to have
• Nice to hace the words: Strategy, execution, results
• Nice to vave the claim: Lantern of the Steady Harvest
• The three colors should be shown:
• cyan for STRATEGY
• green for EXECUTION
• blue for RESULTS
Should not have
• Complete black background

```html
<!DOCTYPE html>
<html lang="en">
<head>
<meta charset="utf-8">
<title>BrivoTerna – Business Card</title>
<link href="https://fonts.googleapis.com/css2?family=Lato:wght@400;700;900&display=swap" rel="stylesheet">
<style>
  :root {
    --backdrop: #dddddd;
    --card: #ffffff;
    --navy: #233a8f;
    --cyan: #29a9e0;
    --green: #8cc63f;
    --grey: #8a8a8a;
    --shadow: rgba(0, 0, 0, 0.45);
  }
  * { margin: 0; padding: 0; box-sizing: border-box; }
  html, body {
    width: 1200px;
    height: 960px;
    overflow: hidden;
    background: var(--backdrop);
    font-family: "Lato", Arial, sans-serif;
  }
  .card {
    position: absolute;
    left: 281px;
    width: 655px;
    height: 374px;
    background: var(--card);
    border-radius: 26px;
    box-shadow: 0 4px 3px var(--shadow);
  }
  .card--front { top: 80px; }
  .card--back { top: 506px; }

  .brand-name {
    position: absolute;
    font-weight: 900;
    color: var(--navy);
    letter-spacing: -0.5px;
    line-height: 1;
    white-space: nowrap;
  }
  .card--front .brand-name {
    left: 52px;
    top: 150px;
    font-size: 42px;
  }
  .holder {
    position: absolute;
    right: 68px;
    top: 92px;
    text-align: right;
  }
  .holder-name {
    font-size: 27px;
    font-weight: 700;
    color: var(--navy);
    line-height: 1.2;
  }
  .holder-role {
    font-size: 17.5px;
    color: var(--grey);
    line-height: 1.3;
  }
  .contacts {
    position: absolute;
    left: 50px;
    top: 251px;
    list-style: none;
  }
  .contacts li {
    display: flex;
    align-items: center;
    height: 24px;
    font-size: 17px;
    color: var(--grey);
  }
  .contacts svg {
    width: 14px;
    height: 14px;
    margin-right: 9px;
    fill: var(--navy);
    flex: none;
  }

  .card--back .brand-name {
    left: 0;
    right: 0;
    top: 200px;
    text-align: center;
    font-size: 54px;
  }
  .tagline {
    position: absolute;
    left: 0;
    right: 0;
    top: 276px;
    text-align: center;
    font-size: 18px;
    color: var(--grey);
    letter-spacing: 0.3px;
  }
  .tagline .strategy { color: var(--cyan); }
  .tagline .execution { color: var(--green); }
  .tagline .results { color: var(--navy); }
  .tagline .sep { margin: 0 6px; }
</style>
</head>
<body>
  <section class="card card--front">
    <div class="brand-name">BrivoTerna</div>

    <div class="holder">
      <div class="holder-name">Teodoro Vinsquel</div>
      <div class="holder-role">CEO &amp; Founder</div>
    </div>

    <ul class="contacts">
      <li>
        <svg viewBox="0 0 16 16" aria-hidden="true"><path d="M4 1.5c.6-.5 1.4-.3 1.7.3l1 2c.3.6.1 1.2-.4 1.6l-.9.6c.5 1.6 1.8 3 3.4 3.6l.6-.9c.4-.5 1-.7 1.6-.4l2 1c.6.3.8 1.1.3 1.7l-1 1.2c-.6.7-1.6 1-2.5.6C6.2 11.5 3.6 8.8 2.3 5.3c-.3-.9 0-1.9.7-2.5z"/></svg>
        +34 655.803.912
      </li>
      <li>
        <svg viewBox="0 0 16 16" aria-hidden="true"><path d="M1 4h14v8H1z M1.8 4.6 8 9l6.2-4.4" fill="none" stroke="currentColor"/><path d="M1 4h14L8 9z M1 12l5-4 2 1.4L10 8l5 4z"/></svg>
        teodoro.vinsquel@brivoterna-example.com
      </li>
      <li>
        <svg viewBox="0 0 16 16" aria-hidden="true"><path d="M8 1a7 7 0 1 0 0 14A7 7 0 0 0 8 1zm0 1.3c.8.6 1.5 1.8 1.8 3.2H6.2C6.5 4.1 7.2 2.9 8 2.3zM2.5 6.8h2.6a11 11 0 0 0 0 2.4H2.5a5.7 5.7 0 0 1 0-2.4zm3.9 0h3.2a9.5 9.5 0 0 1 0 2.4H6.4a9.5 9.5 0 0 1 0-2.4zm4.5 0h2.6a5.7 5.7 0 0 1 0 2.4h-2.6a11 11 0 0 0 0-2.4zM3 5.5a5.7 5.7 0 0 1 2.6-2.5c-.5.7-.8 1.6-1 2.5zm7.4-2.5A5.7 5.7 0 0 1 13 5.5h-1.6c-.2-.9-.5-1.8-1-2.5zM3 10.5h1.6c.2.9.5 1.8 1 2.5A5.7 5.7 0 0 1 3 10.5zm3.2 0h3.6c-.3 1.4-1 2.6-1.8 3.2-.8-.6-1.5-1.8-1.8-3.2zm5.2 0H13a5.7 5.7 0 0 1-2.6 2.5c.5-.7.8-1.6 1-2.5z"/></svg>
        www.brivoterna-example.com
      </li>
    </ul>
  </section>

  <section class="card card--back">
    <div class="brand-name">BrivoTerna</div>
    <p class="tagline">
      <span class="strategy">STRATEGY</span><span class="sep">-</span><span class="execution">EXECUTION</span><span class="sep">-</span><span class="results">RESULTS</span>
    </p>
  </section>
</body>
</html>
```